Refresh Velquor Web Presence - www.velquor-sample.com

Velquor (www.velquor-sample.com)web site needs a makeover. It needs to be more modern, less cluttered, more corporate, prestigious, user friendly, impressive, up to date. We want a modern corporate image that encourages our business users to trust us and buy our products and services. They need to understand that they are dealing with a highly reputable, long established company, but one that is up to date and forward thinking.
1. Clean uncluttered design.
2. Domain Registration box and Countries (price) box to be collapsible and expandable.
3. All links on page need to be conserved for SEO but hidden from view.
4. Logo and general colour scheme need to be retained.
5. Phone number to be prominently displayed at top of page.
6. No calls to action (CTA) below the fold.
7. Sites we like: www.brinzal-sample.com, www.tundexa-sample.com,www.qop.com,www.plavion-sample.com, www.fismet-sample.com (busy but clear CTAs), www.yarmel-sample.com
Reason: We lost a lot of time to review over the holiday weekend. We need to have a chance to interact during business hours.
Target Market(s)
Small business to large enterprise
Industry/Entity Type
Business
Look and feel

```html
<!DOCTYPE html>
<html lang="en">
<head>
<meta charset="utf-8">
<title>Velquor – Domain Names</title>
<link rel="stylesheet" href="https://fonts.googleapis.com/css2?family=Oswald:wght@400;500&family=Open+Sans:wght@400;600&family=Signika:wght@400;600&display=swap">
<style>
:root{
  --navy:#2e3384;
  --navy-dark:#262a70;
  --orange:#ee6f12;
  --orange-light:#f8922c;
  --text:#333;
  --muted:#9a9a9a;
  --sky-1:#e4f3fb;
  --sky-2:#bfe1f3;
  --panel:#f3f3f3;
  --line:#cfcfcf;
  --social:#8c8c8c;
}
*{box-sizing:border-box;margin:0;padding:0}
html,body{width:1200px;height:846px;overflow:hidden}
body{position:relative;font-family:"Open Sans",Arial,sans-serif;color:var(--text);background:var(--panel)}
.abs{position:absolute}

/* top bar */
.topbar{left:0;top:0;width:1200px;height:34px;background:linear-gradient(var(--navy),var(--navy-dark));color:#fff;font-size:12px}
.topbar .chat{left:172px;top:9px;display:flex;align-items:center;gap:5px}
.whois{left:263px;top:7px;width:148px;height:20px;background:#fff;display:flex}
.whois span{flex:1;color:#666;font-size:11px;padding:2px 6px}
.whois b{width:21px;background:var(--orange);display:flex;align-items:center;justify-content:center}
.toplink{top:9px}
.login{left:804px;top:0;width:70px;height:34px;background:var(--orange);font-size:13px;display:flex;align-items:center;justify-content:center;gap:6px}
.phone{left:887px;top:4px;font-family:"Oswald",sans-serif;font-size:20px;display:flex;align-items:center;gap:6px}

/* header */
.header{left:0;top:34px;width:1200px;height:82px;background:linear-gradient(#fff,#ececec);border-bottom:1px solid #c9c9c9}
.logo{left:174px;top:18px;display:flex;align-items:center;gap:8px;font-family:"Open Sans",sans-serif;font-weight:600;font-size:34px;color:var(--navy)}
.logo i{width:28px;height:28px;border-radius:50%;background:var(--orange);display:block}
.nav{left:397px;top:38px;display:flex;gap:19px;font-size:14px;color:#222}
.nav .active{color:var(--orange);border-bottom:2px solid var(--orange);padding-bottom:6px;position:relative}

/* hero */
.hero{left:0;top:117px;width:1200px;height:333px;background:linear-gradient(100deg,var(--sky-1) 0%,#f4fafd 45%,var(--sky-2) 100%)}
.headline{left:176px;top:28px;font-family:"Oswald",sans-serif;color:var(--navy);line-height:1}
.headline .big{font-size:96px;font-weight:500;letter-spacing:-1px}
.headline .mid{font-size:58px}
.headline .line2{display:block;font-size:58px;margin-top:-4px}
.tagline{left:176px;top:220px;font-size:26px;color:var(--orange)}
.cta{left:180px;top:287px;width:209px;height:46px;background:linear-gradient(var(--orange-light),var(--orange));color:#fff;font-family:"Signika",sans-serif;font-weight:600;font-size:24px;display:flex;align-items:center;justify-content:center;gap:10px;border-radius:3px 3px 0 0}
.globe{left:685px;top:18px;width:295px;height:300px;border-radius:50%;background:radial-gradient(circle at 45% 45%,#d9d6cf 0%,#8c877d 45%,rgba(120,160,200,.25) 72%,rgba(255,255,255,0) 73%)}
.slider{left:965px;top:311px;display:flex;gap:1px}
.slider span{width:20px;height:22px;background:var(--navy);color:#fff;font-size:13px;display:flex;align-items:center;justify-content:center}
.contact{left:1160px;top:93px;width:40px;height:120px;background:var(--orange);color:#fff;border-radius:6px 0 0 6px;font-family:"Signika",sans-serif;font-weight:600;font-size:13px;letter-spacing:1px;writing-mode:vertical-rl;transform:rotate(180deg);display:flex;align-items:center;justify-content:center}
.social{left:1165px;top:362px;display:flex;flex-direction:column;gap:5px}
.social span{width:31px;height:31px;border-radius:50%;background:var(--social);border:2px solid #fff;box-shadow:0 0 2px #999}
.social span:first-child{background:var(--navy)}

/* search area */
.tabs{left:172px;top:493px;display:flex;align-items:center;font-family:"Signika",sans-serif;font-size:17px;color:#333}
.tabs span{padding:6px 11px}
.tabs .current{background:linear-gradient(#ddd,#f3f3f3);padding:6px 11px}
.country{left:866px;top:495px;width:141px;height:28px;background:var(--orange);color:#fff;font-family:"Signika",sans-serif;font-weight:600;font-size:14px;border-radius:3px;display:flex;align-items:center;justify-content:center;gap:6px}
.www{left:172px;top:576px;font-family:"Signika",sans-serif;font-weight:600;font-size:28px;color:var(--navy)}
.search{left:263px;top:567px;width:744px;height:54px;background:#fff;border:2px solid var(--line);border-radius:3px}
.search span{position:absolute;left:18px;top:9px;font-size:28px;color:var(--muted)}
.search-btn{left:778px;top:567px;width:229px;height:54px}
.search-btn b{position:absolute;left:48px;top:8px;font-family:"Oswald",sans-serif;font-weight:500;font-size:32px;color:#fff;letter-spacing:1px}

.filter{left:173px;top:658px;width:834px;height:165px;background:#fafafa;border:1px solid var(--line)}
.filter-head{left:0;top:0;width:832px;height:38px;background:var(--navy);color:#fff;font-family:"Signika",sans-serif;font-weight:600;font-size:15px}
.filter-head .pointer{position:absolute;left:55px;top:37px;width:0;height:0;border-left:60px solid transparent;border-right:60px solid transparent;border-top:10px solid var(--navy)}
.box{position:absolute;display:flex;align-items:center;gap:8px;font-size:13px}
.box i{width:17px;height:17px;border:1px solid #888;background:#fff;display:block;position:relative}
.filter-head .box i{border-color:#ccc}
.box i svg{position:absolute;left:1px;top:-6px}
.more{left:508px;top:808px;width:167px;height:25px;background:#fff;border:1px solid var(--line);border-radius:12px;color:var(--orange);font-family:"Signika",sans-serif;font-weight:600;font-size:12px;display:flex;align-items:center;justify-content:center;gap:5px}
</style>
</head>
<body>

<header class="abs topbar">
  <div class="abs chat"><svg width="14" height="12" viewBox="0 0 14 12"><path d="M7 1C3.5 1 1 3 1 5.3c0 1.3.8 2.4 2 3.1L2.5 11l3-2c.5.1 1 .1 1.5.1 3.5 0 6-2 6-3.8S10.5 1 7 1z" fill="#fff"/></svg>Chat with us</div>
  <div class="abs whois"><span>Whois Seach</span><b><svg width="11" height="11" viewBox="0 0 11 11"><circle cx="4.5" cy="4.5" r="3.2" stroke="#fff" stroke-width="1.6" fill="none"/><path d="M7 7l3 3" stroke="#fff" stroke-width="1.8"/></svg></b></div>
  <span class="abs toplink" style="left:570px">Register</span>
  <span class="abs toplink" style="left:627px">Shopping Cart</span>
  <span class="abs toplink" style="left:720px">View Cart (0)</span>
  <div class="abs login">Login <svg width="10" height="7" viewBox="0 0 10 7"><path d="M0 0h10L5 7z" fill="#fff"/></svg></div>
  <div class="abs phone"><svg width="8" height="14" viewBox="0 0 8 14"><rect x=".5" y=".5" width="7" height="13" rx="1.5" fill="none" stroke="#fff"/><rect x="2" y="2.5" width="4" height="6" fill="#fff"/></svg>+1.5550142087</div>
</header>

<div class="abs header">
  <div class="abs logo"><i></i>Velquor</div>
  <nav class="abs nav">
    <span class="active">Domain Names</span><span>IDN Domains</span><span>New gTLDs</span><span>Phone Numbers</span><span>Hosting</span><span>Resellers</span><span>About Us</span>
  </nav>
</div>

<section class="abs hero">
  <h1 class="abs headline"><span class="big">300</span><span class="mid">+ Domain</span><span class="line2">Name Extensions</span></h1>
  <p class="abs tagline">Accredited in over 100 countries</p>
  <div class="abs cta">View Pricing <svg width="18" height="20" viewBox="0 0 18 20"><path d="M0 1l8 9-8 9zM9 1l8 9-8 9z" fill="#fff"/></svg></div>
  <svg class="abs" style="left:403px;top:295px" width="114" height="28" viewBox="0 0 114 28"><path d="M112 4C80 3 40 12 4 16" stroke="#4a4fa5" stroke-width="2" fill="none"/><path d="M16 6L3 16l14 9" stroke="#4a4fa5" stroke-width="2" fill="none"/></svg>
  <div class="abs globe" role="img" aria-label="Illustration of a globe surrounded by coloured spheres labelled with domain extensions"></div>
  <div class="abs slider"><span>&lsaquo;</span><span>&rsaquo;</span></div>
  <div class="abs contact">CONTACT US</div>
  <div class="abs social"><span></span><span></span><span></span><span></span><span></span></div>
</section>

<div class="abs tabs"><span class="current">Domain Registration</span><span>IDN</span><span>Bulk Search</span><span>Transfer</span><span>Renew</span><span>Map Search</span><span>PhNUM</span></div>
<div class="abs country">Select Country <svg width="11" height="8" viewBox="0 0 11 8"><path d="M0 0h11L5.5 8z" fill="#fff"/></svg></div>

<div class="abs www">www.</div>
<div class="abs search"><span>Search for a new domain</span></div>
<svg class="abs search-btn" viewBox="0 0 229 54" width="229" height="54"><defs><linearGradient id="sb" x1="0" y1="0" x2="0" y2="1"><stop offset="0" stop-color="#f8922c"/><stop offset="1" stop-color="#e6620b"/></linearGradient></defs><path d="M0 0h226a3 3 0 0 1 3 3v48a3 3 0 0 1-3 3H0l14-27z" fill="url(#sb)"/><circle cx="182" cy="23" r="9" stroke="#fff" stroke-width="3" fill="none"/><path d="M189 30l9 10" stroke="#fff" stroke-width="4"/></svg>
<div class="abs search-btn"><b>SEARCH</b></div>

<div class="abs filter">
  <div class="abs filter-head">
    <div class="pointer"></div>
    <div class="box" style="left:20px;top:10px"><i></i>Generic</div>
    <div class="box" style="left:132px;top:10px"><i></i>Europe</div>
    <div class="box" style="left:241px;top:10px"><i><svg width="20" height="20" viewBox="0 0 20 20"><path d="M2 12l5 6 11-16" stroke="#fff" stroke-width="2.5" fill="none"/></svg></i>Asia/Pacific</div>
    <div class="box" style="left:379px;top:10px"><i></i>America</div>
    <div class="box" style="left:494px;top:10px"><i></i>Africa</div>
    <div class="box" style="left:606px;top:10px"><i></i>All Domains</div>
  </div>
  <div class="box" style="left:30px;top:68px"><i></i>.biz</div>
  <div class="box" style="left:120px;top:68px"><i></i>.co</div>
  <div class="box" style="left:214px;top:68px"><i><svg width="20" height="20" viewBox="0 0 20 20"><path d="M2 12l5 6 11-16" stroke="#2e3384" stroke-width="2.5" fill="none"/></svg></i>.com</div>
  <div class="box" style="left:309px;top:68px"><i></i>.info</div>
  <div class="box" style="left:400px;top:68px"><i></i>.mobi</div>
  <div class="box" style="left:493px;top:68px"><i><svg width="20" height="20" viewBox="0 0 20 20"><path d="M2 12l5 6 11-16" stroke="#2e3384" stroke-width="2.5" fill="none"/></svg></i>.name</div>
  <div class="box" style="left:586px;top:68px"><i></i>.net</div>
  <div class="box" style="left:657px;top:68px"><i></i>.me</div>
  <div class="box" style="left:729px;top:68px"><i></i>.org</div>
  <div class="box" style="left:30px;top:111px"><i></i>.pro</div>
  <div class="box" style="left:120px;top:111px;font-size:12px"><i></i>.pty-ltd.com</div>
  <div class="box" style="left:214px;top:111px"><i><svg width="20" height="20" viewBox="0 0 20 20"><path d="M2 12l5 6 11-16" stroke="#2e3384" stroke-width="2.5" fill="none"/></svg></i>.tel</div>
  <div class="box" style="left:309px;top:111px"><i></i>.travel</div>
  <div class="box" style="left:400px;top:111px"><i></i>.xxx</div>
</div>
<div class="abs more">Show More Extensions <svg width="12" height="10" viewBox="0 0 12 10"><path d="M0 0h12L6 5zM0 5h12L6 10z" fill="#ee6f12"/></svg></div>

</body>
</html>
```